Marwick Law Letterhead

We need a new letterhead design for a Law Firm. The address for the law firm is 1475 Calloway Street, Suite 210, Houston, Texas 77041. Phone Number: 832-361-9027; Fax Number: 832-614-7359. The logo is uploaded to the project.

```html
<!DOCTYPE html>
<html lang="en">
<head>
<meta charset="utf-8">
<title>Marwick Law Letterhead</title>
<link href="https://fonts.googleapis.com/css2?family=Montserrat:wght@400;500;600&display=swap" rel="stylesheet">
<style>
  :root {
    --backdrop: #e8e8e8;
    --paper: #ffffff;
    --navy: #1c2f5e;
    --red: #d71f26;
    --red-deep: #7c0c14;
    --ink: #2b2b2b;
  }
  * { box-sizing: border-box; margin: 0; padding: 0; }
  html, body {
    width: 1154px; height: 1200px; overflow: hidden;
    background: var(--backdrop);
    font-family: "Montserrat", Arial, sans-serif;
  }
  .letterhead {
    position: absolute; left: 162px; top: 20px;
    width: 830px; height: 1160px;
    background: var(--paper);
    box-shadow: 0 4px 14px rgba(0,0,0,.18);
    overflow: hidden;
    color: var(--ink);
  }
  .brand {
    position: absolute; left: 32px; top: 92px;
    display: flex; align-items: center; gap: 12px;
  }
  .brand-dot { width: 18px; height: 18px; border-radius: 50%; background: var(--red); }
  .brand-name { font-size: 31px; font-weight: 600; color: var(--navy); letter-spacing: .5px; }
  .contact {
    position: absolute; left: 609px; top: 72px; height: 99px;
    border-left: 1.5px solid var(--red);
    padding-left: 21px;
    font-size: 14px; line-height: 18px; color: #1a1a1a;
    font-style: normal;
  }
  .contact-address { margin-bottom: 10px; }
  .contact-line { display: flex; align-items: center; gap: 10px; }
  .contact-line svg { width: 12px; height: 12px; fill: var(--red); }
  .recipient {
    position: absolute; left: 31px; top: 258px;
    font-size: 14px; line-height: 20.7px;
  }
  .body-copy {
    position: absolute; left: 32px; top: 346px; width: 770px;
    font-size: 13.5px; line-height: 20.6px; text-align: justify;
    hyphens: auto;
  }
  .body-copy p { margin-bottom: 20.6px; }
  .closing { position: absolute; left: 31px; top: 839px; font-size: 16.5px; }
  .signature {
    position: absolute; left: 29px; top: 868px; width: 94px; height: 27px;
    background: linear-gradient(90deg, #e6e6e6, #f3f3f3);
    border-radius: 3px;
  }
  .footer-band {
    position: absolute; left: 0; bottom: 0; width: 830px; height: 90px;
    background: linear-gradient(180deg, var(--navy) 0%, var(--red) 55%, var(--red-deep) 100%);
  }
</style>
</head>
<body>
<main class="letterhead">
  <div class="brand">
    <span class="brand-dot"></span>
    <span class="brand-name">Marwick Law</span>
  </div>

  <address class="contact">
    <div class="contact-address">1475 Calloway Street,<br>Suite 210, Houston,<br>Texas 77041</div>
    <div class="contact-line">
      <svg viewBox="0 0 24 24" aria-hidden="true"><path d="M6.6 10.8a15.1 15.1 0 0 0 6.6 6.6l2.2-2.2a1 1 0 0 1 1-.25 11.4 11.4 0 0 0 3.6.57 1 1 0 0 1 1 1V20a1 1 0 0 1-1 1A17 17 0 0 1 3 4a1 1 0 0 1 1-1h3.5a1 1 0 0 1 1 1c0 1.25.2 2.450.57 3.57a1 1 0 0 1-.25 1z"/></svg>
      <span>832-361-9027</span>
    </div>
    <div class="contact-line">
      <svg viewBox="0 0 24 24" aria-hidden="true"><path d="M6 2h12v6H6zM4 9h16a2 2 0 0 1 2 2v6h-4v5H6v-5H2v-6a2 2 0 0 1 2-2zm4 8v3h8v-3z"/></svg>
      <span>832-614-7359</span>
    </div>
  </address>

  <div class="recipient">
    Mr/s<br>First Name and Last Name<br>Company Name<br>Address
  </div>

  <div class="body-copy">
    <p>Lorem ipsum dolor sit amet,consectetur adipiscing sed do eiusmod tempor incididunt laboreet dolore magna aliqua.Ut enim ad minim.veniam, quis nostrud exercitation ullamco laboris nisi ut aliquip exea commodo consequat.Lorem ipsum dolor sit amet,consectetur adipiscing sed do eiusmod tempor incididunt.labore et dolore magna aliqua. Ut enim</p>
    <p>Lorem ipsum dolor sit amet, consectetur adipiscing sed do eiusmod tempor incididunt labore et dolore magna aliqua. Ut enim ad minim veniam, quis nostrud exercitation ullamco laboris nisi ut aliquip exea commodo consequat.Duis aute irure dolor in reprehenderit in voluptate velit esse cillum irure dolor in reprehenderit in voluptate velit esse irure</p>
    <p>Lorem ipsum dolor sit amet, consectetur adipiscing sed do eiusmod tempor incididunt labore et dolore magna aliqua. consequat. Duis aute irure dolor in.reprehenderit in voluptate velit esse cillum dolore eu fugiat nulla pariatur. Excepteur sint occaecat cupidatat non proident, sunt in culpa qui officia deserunt mollit,</p>
    <p>Lorem ipsum dolor sit amet, consectetur adipiscing sed do eiusmod tempor incididunt labore et dolore magna aliqua. Ut enim Lorem ipsum dolor sit amet, consectetur adipiscing sed do eiusmod tempor incididunt labore et dolore magna aliqua. Ut enim Lorem ipsum aliqua.ipsum</p>
    <p>Lorem ipsum dolor sit amet, consectetur adipiscing sed do eiusmod tempor incididunt labore et dolore magna aliqua. Ut enim ad minim veniam, quis nostrud exercitation ullamco laboris nisi ut aliquip exea commodo consequat.Duis aute irure dolor in reprehenderit in voluptate velit esse cillum irure dolor in reprehenderit in voluptate velit esse irure</p>
  </div>

  <div class="closing">Regards</div>
  <div class="signature" role="img" aria-label="Handwritten signature of the sender"></div>

  <div class="footer-band" role="img" aria-label="Decorative navy and red footer band"></div>
</main>
</body>
</html>
```